Business Card for a Jewellery Brand

Business card for an upscale jewellery brand. Attached is the brand logo and icon and color board. I am looking for two card versions: one for the founder and one is generic. The card should be elegant and convey upscale and premium feel. I am open to both square and rectangle card shapes.

Industry/Entity Type

Jewelry

Contact Information for Business Card

Two cards: (1) Sunela Parvaniya (Founder) (2) General
(1) Sunela Parvaniya card should have Name: Sunela Parvaniya, Title: Founder Email id: sunela@quiremo.com.au. Phone no: +61452913307
(2) Generic card should have Email id: info@quiremo.com.au. Phone no: +61436207518

Requirements
Must have
• Workmark
• ICON
• Phone no
• Email ID
• ABN: 58219740312 (Note: ABN is Business number in Australia)
• Website: www.quiremo.com.au
• Instagram: quiremo_jewellery
• Facebook: @quiremojewellery
Nice to have
• Tagline

```html
<!DOCTYPE html>
<html lang="en">
<head>
<meta charset="utf-8">
<title>Quiremo Business Card</title>
<link href="https://fonts.googleapis.com/css2?family=Roboto:wght@300;400;500&display=swap" rel="stylesheet">
<style>
  :root {
    --backdrop: #333135;
    --blush: #e2a9a6;
    --blush-deep: #e19a93;
    --blush-faint: #f6e5e4;
    --paper: #ffffff;
    --ink: #1f1d1f;
  }
  * { box-sizing: border-box; margin: 0; padding: 0; }
  html, body {
    width: 1200px; height: 1200px; overflow: hidden;
    background: var(--backdrop);
    font-family: "Roboto", Arial, sans-serif;
  }
  .canvas {
    width: 1200px; height: 1200px;
    display: flex; flex-direction: column; align-items: center; justify-content: center;
    gap: 40px;
  }
  .card {
    width: 900px; height: 520px; position: relative; overflow: hidden;
  }
  .card-front {
    background: var(--blush);
    display: flex; flex-direction: column; align-items: center; justify-content: center; gap: 26px;
  }
  .front-mark {
    width: 110px; height: 110px; border: 6px solid var(--paper); border-radius: 50%;
  }
  .front-wordmark {
    color: var(--paper); font-weight: 400; font-size: 64px; letter-spacing: 22px; padding-left: 22px;
  }
  .card-back { background: var(--paper); }
  .back-decoration {
    position: absolute; right: -60px; top: 40px;
    width: 360px; height: 360px; border-radius: 50%;
    border: 38px solid var(--blush-faint);
  }
  .back-brand {
    position: absolute; left: 70px; top: 60px;
    display: flex; flex-direction: column; align-items: flex-start; gap: 18px;
  }
  .back-mark {
    width: 70px; height: 70px; border: 5px solid var(--blush); border-radius: 50%; margin-left: 60px;
  }
  .back-wordmark {
    color: var(--blush); font-weight: 400; font-size: 44px; letter-spacing: 14px;
  }
  .person {
    position: absolute; left: 70px; top: 240px;
  }
  .person-name { color: var(--blush-deep); font-weight: 300; font-size: 30px; }
  .person-title { color: var(--ink); font-weight: 400; font-size: 21px; margin-top: 4px; }
  .divider {
    position: absolute; left: 60px; right: 60px; top: 330px; height: 3px; background: var(--blush-deep);
  }
  .contacts {
    position: absolute; left: 60px; top: 350px;
    display: grid; grid-template-columns: 245px 260px; row-gap: 12px;
    font-size: 20px; color: var(--ink);
  }
  .contact { display: flex; align-items: center; gap: 10px; white-space: nowrap; }
  .contact svg { width: 16px; height: 16px; flex: none; }
  .social-dot { width: 14px; height: 14px; border-radius: 50%; background: var(--blush-deep); flex: none; }
  .social-square { width: 14px; height: 14px; background: var(--blush-deep); flex: none; }
  .address {
    position: absolute; right: 60px; top: 350px; text-align: right;
    font-size: 20px; color: var(--ink); line-height: 1.45;
  }
  .address-label { color: var(--blush-deep); font-weight: 300; font-size: 19px; }
</style>
</head>
<body>
<main class="canvas">
  <section class="card card-front">
    <div class="front-mark"></div>
    <div class="front-wordmark">QUIREMO</div>
  </section>

  <section class="card card-back">
    <div class="back-decoration"></div>
    <div class="back-brand">
      <div class="back-mark"></div>
      <div class="back-wordmark">QUIREMO</div>
    </div>
    <div class="person">
      <p class="person-name">Sunela Parvaniya</p>
      <p class="person-title">Founder</p>
    </div>
    <div class="divider"></div>
    <div class="contacts">
      <div class="contact">
        <svg viewBox="0 0 16 16"><path d="M4 1.5l2.5 3-1.6 1.6a9 9 0 0 0 5 5l1.6-1.6 3 2.5-1.5 2.5C7.5 14.5 1.5 8.5 1.5 3z" fill="#e19a93"/></svg>
        +61452913307
      </div>
      <div class="contact">
        <svg viewBox="0 0 16 16"><rect x="1" y="3" width="14" height="10" fill="#e19a93"/><path d="M1 3l7 6 7-6" fill="none" stroke="#fff" stroke-width="1.3"/></svg>
        sunela@quiremo.com.au
      </div>
      <div class="contact"><span class="social-dot"></span>quiremo_jewellery</div>
      <div class="contact"><span class="social-square"></span>@quiremojewellery</div>
      <div class="contact">
        <svg viewBox="0 0 16 16"><g fill="none" stroke="#e19a93" stroke-width="1.3"><circle cx="8" cy="8" r="6.5"/><ellipse cx="8" cy="8" rx="3" ry="6.5"/><path d="M1.5 8h13"/></g></svg>
        www.quiremo.com.au
      </div>
    </div>
    <div class="address">
      <p class="address-label">Address</p>
      <p>742 Harlow Street, Suite 310</p>
      <p>Fenwick, Victoria 3041</p>
    </div>
  </section>
</main>
</body>
</html>
```